Business Card for Coastal Tundrabridge Advisory

We need a business card for Coastal Tundrabridge Advisory. The company website address is provided below. The company logo is attached. We provide specialized permafrost services to the mining, transportation, and oil & gas industries. The card should be prepared for:
Matthias Korhonen, PhD.
Coastal Tundrabridge Advisory
PO Box 418259
Quillwater, Alaska 99642
Direct: +1-907-555-0143
Email: mkorhonen@tundrabridgeadvisory.example
Website: www.coastaltundrabridgeadvisory.example

```html
<!DOCTYPE html>
<html lang="en">
<head>
<meta charset="utf-8">
<title>Coastal Tundrabridge Advisory — Business Card</title>
<link rel="stylesheet" href="https://fonts.googleapis.com/css2?family=Montserrat:wght@400;500;600;700&display=swap">
<style>
  :root {
    --stage: #5e4a36;
    --card-light: #ffffff;
    --card-dark: #121a22;
    --card-dark-edge: #0b1016;
    --ink: #14181d;
    --ink-soft: #2a2f35;
    --rule: #1b1f24;
    --paper-white: #ffffff;
    --pattern-light: #6f757b;
    --pattern-dark: #10161d;
  }
  * { box-sizing: border-box; margin: 0; padding: 0; }
  html, body {
    width: 900px; height: 1200px; overflow: hidden;
    background: var(--stage);
    font-family: "Montserrat", sans-serif;
  }
  .canvas { position: relative; width: 900px; height: 1200px; }

  .card {
    position: absolute; border-radius: 22px;
    box-shadow: 0 10px 24px rgba(0,0,0,0.35);
    overflow: hidden;
  }
  .card-front { left: 80px; top: 131px; width: 742px; height: 440px; background: var(--card-light); color: var(--ink); }
  .card-back { left: 78px; top: 638px; width: 744px; height: 440px; background: var(--card-dark); }

  .brand-name {
    font-weight: 700; text-transform: uppercase; letter-spacing: 1px;
    line-height: 1.15; text-align: center;
  }
  .front-brand {
    position: absolute; left: 45px; top: 212px; width: 270px;
    font-size: 19px; color: var(--ink);
  }

  .divider { position: absolute; left: 316px; top: 160px; width: 2px; height: 144px; background: var(--rule); }

  .holder { position: absolute; left: 328px; top: 158px; }
  .holder-name { font-size: 22px; font-weight: 600; color: var(--ink); line-height: 1.2; }
  .holder-title { font-size: 15px; font-weight: 400; color: var(--ink-soft); margin-top: 3px; }

  .contact-list { position: absolute; left: 330px; top: 221px; list-style: none; }
  .contact-item {
    display: flex; align-items: center; height: 31px;
    font-size: 15.5px; color: var(--ink);
  }
  .contact-icon { width: 16px; height: 16px; margin-right: 14px; fill: var(--ink); flex: none; }

  .address {
    position: absolute; left: 0; right: 0; top: 384px;
    text-align: center; font-size: 15.5px; color: var(--ink);
  }

  .back-pattern {
    position: absolute; inset: 0;
    background: linear-gradient(90deg, var(--pattern-light) 0%, #3a4148 28%, var(--pattern-dark) 62%, var(--card-dark-edge) 100%);
    opacity: 0.55;
  }
  .back-brand {
    position: absolute; left: 0; right: 0; top: 336px;
    font-size: 19px; color: var(--paper-white);
  }
</style>
</head>
<body>
<div class="canvas">
  <section class="card card-front" aria-label="Card front">
    <div class="brand-name front-brand">Coastal Tundrabridge<br>Advisory</div>
    <div class="divider"></div>
    <div class="holder">
      <div class="holder-name">Matthias Korhonen, PhD.</div>
      <div class="holder-title">Managing Director</div>
    </div>
    <ul class="contact-list">
      <li class="contact-item">
        <svg class="contact-icon" viewBox="0 0 24 24"><path d="M6.6 10.8a15.1 15.1 0 0 0 6.6 6.6l2.2-2.2a1 1 0 0 1 1-.25 11.4 11.4 0 0 0 3.6.57 1 1 0 0 1 1 1V20a1 1 0 0 1-1 1A17 17 0 0 1 3 4a1 1 0 0 1 1-1h3.5a1 1 0 0 1 1 1c0 1.25.2 2.45.57 3.57a1 1 0 0 1-.25 1z"/></svg>
        +1-907-555-0143
      </li>
      <li class="contact-item">
        <svg class="contact-icon" viewBox="0 0 24 24"><path d="M3 5h18v14H3z M4.5 6.5 12 12l7.5-5.5" fill="none" stroke="currentColor"/><path d="M3 5h18v2l-9 6-9-6zM3 9l9 6 9-6v10H3z"/></svg>
        mkorhonen@tundrabridgeadvisory.example
      </li>
      <li class="contact-item">
        <svg class="contact-icon" viewBox="0 0 24 24"><circle cx="12" cy="12" r="9" fill="none" stroke="#14181d" stroke-width="2"/><path d="M7 7c2 1 3 3 2 5s1 3 3 3l-1 5M14 4c0 2 2 3 4 3M15 13c2 0 4 1 5 2" fill="none" stroke="#14181d" stroke-width="2"/></svg>
        www.coastaltundrabridgeadvisory.example
      </li>
    </ul>
    <div class="address">PO Box 418259 Quillwater, Alaska 99642</div>
  </section>

  <section class="card card-back" aria-label="Card back">
    <div class="back-pattern" role="img" aria-label="Repeating tonal company name pattern fading from grey to black"></div>
    <div class="brand-name back-brand">Coastal Tundrabridge<br>Advisory</div>
  </section>
</div>
</body>
</html>
```